U.S. Popcorn company needs business cards

We are a popcorn company that manufactures popcorn and sells it to grocery stores worldwide. Our theme is "Americana" and our logo is U.S. route 66 which is the most famous highway in the U.S.

We would like the design to be simple and to use both sides. On the back side we would like to see just the logo and website. The front would be normal details

Target Market(s)

Wholesalers, grocers and distributors

Industry/Entity Type

Manufacture

Contact Information for Business Card

Business name: Prairie Lantern Popcorn
Phone: +1 555 308 4726
Email: Dale@prairielanternpopcorn.com
website: www.prairielanternpopcorn.com
Tag Line: "GOLDEN IN EVERY BITE"
Name: Dale Whitcombe
Title: Founder/President

Requirements
Must have
• Either this design should be fun or clean and simple. I will let you show me your thougths.
Nice to have
• Anything that ties in the real Hwy Route 66.
• Colors might need to be red, white and blue incorporated.
Should not have
• Not be too busy.

```html
<!DOCTYPE html>
<html lang="en">
<head>
<meta charset="utf-8">
<title>Prairie Lantern Popcorn – Business Cards</title>
<link rel="stylesheet" href="https://fonts.googleapis.com/css2?family=Source+Sans+3:wght@400;600;700&display=swap">
<style>
  :root {
    --backdrop: #3b342f;
    --card: #121212;
    --card-edge: #1c1c1c;
    --red: #e0262b;
    --blue: #1f3a93;
    --white: #f2f2f2;
    --font: "Source Sans 3", Arial, sans-serif;
  }
  * { box-sizing: border-box; margin: 0; padding: 0; }
  html, body {
    width: 1200px; height: 844px; overflow: hidden;
    background: var(--backdrop);
    font-family: var(--font);
  }
  .canvas {
    position: relative; width: 1200px; height: 844px;
    display: flex; align-items: center; justify-content: center; gap: 48px;
  }
  .card {
    position: relative; width: 520px; height: 297px;
    background: var(--card);
    border: 1px solid var(--card-edge);
    box-shadow: 0 12px 30px rgba(0,0,0,.45);
    color: var(--white);
  }
  .brand {
    position: absolute; left: 0; right: 0;
    display: flex; align-items: center; justify-content: center; gap: 10px;
  }
  .brand-dot {
    width: 16px; height: 16px; border-radius: 50%; background: var(--blue);
  }
  .brand-name {
    font-weight: 700; font-size: 24px; color: var(--red);
    letter-spacing: .5px; text-transform: uppercase;
  }
  .card-front .brand { top: 62px; }
  .person {
    position: absolute; right: 32px; top: 124px; text-align: left;
  }
  .person-name { color: var(--red); font-weight: 600; font-size: 19px; line-height: 1.1; }
  .person-title { color: var(--white); font-size: 14px; line-height: 1.3; }
  .rule {
    position: absolute; left: 0; right: 0; height: 2px; background: var(--red);
  }
  .rule-top { top: 172px; }
  .rule-bottom { bottom: 16px; }
  .contacts {
    position: absolute; left: 24px; top: 196px; list-style: none;
  }
  .contacts li {
    display: flex; align-items: center; gap: 10px;
    font-size: 14px; line-height: 20px; color: var(--white);
  }
  .contacts svg { width: 11px; height: 11px; fill: var(--red); flex: none; }
  .tagline {
    position: absolute; right: 40px; bottom: 30px;
    color: var(--red); font-weight: 600; font-size: 17px; letter-spacing: .3px;
  }
  .card-back .brand { top: 112px; }
  .website {
    position: absolute; left: 0; right: 0; top: 168px; text-align: center;
    color: var(--red); font-weight: 600; font-size: 14px;
  }
</style>
</head>
<body>
<main class="canvas">
  <section class="card card-front" aria-label="Business card front">
    <div class="brand">
      <span class="brand-dot"></span>
      <span class="brand-name">Prairie Lantern Popcorn</span>
    </div>
    <div class="person">
      <p class="person-name">Dale Whitcombe</p>
      <p class="person-title">Founder/President</p>
    </div>
    <div class="rule rule-top"></div>
    <ul class="contacts">
      <li>
        <svg viewBox="0 0 12 12" aria-hidden="true"><path d="M2.5 0.5 L4.5 2.8 L3.5 4 Q4.5 6.5 7.9 8.5 L9 7.4 L11.5 9.5 L10 11.5 Q4 11 0.5 2 Z"/></svg>
        +1 555 308 4726
      </li>
      <li>
        <svg viewBox="0 0 12 12" aria-hidden="true"><path d="M0 2 H12 V10 H0 Z M0.8 2.6 L6 6.6 L11.2 2.6 V3.6 L6 7.6 L0.8 3.6 Z" fill-rule="evenodd"/></svg>
        Dale@prairielanternpopcorn.com
      </li>
      <li>
        <svg viewBox="0 0 12 12" aria-hidden="true"><circle cx="6" cy="6" r="5.5"/><path d="M3 3.5 Q5 4 4.5 6 Q6 7 5.5 9.5 M8 2.5 Q7 4.5 9 5.5" stroke="#121212" stroke-width="1" fill="none"/></svg>
        www.prairielanternpopcorn.com
      </li>
    </ul>
    <p class="tagline">GOLDEN IN EVERY BITE</p>
    <div class="rule rule-bottom"></div>
  </section>

  <section class="card card-back" aria-label="Business card back">
    <div class="brand">
      <span class="brand-dot"></span>
      <span class="brand-name">Prairie Lantern Popcorn</span>
    </div>
    <p class="website">www.prairielanternpopcorn.com</p>
  </section>
</main>
</body>
</html>
```